Harrow Tavern & Grille Menu Makeover

I am looking for a professional look to update our current menu. We are an independently owned sports bar and grill. Up to this point, I have done all of my own graphic designing. I am looking for something classy/family oriented. We are a very family friendly sports bar that offers a wide variety of menu options. Our website is www.harrowtavernco.example. This may help you get more of a feel for what type of place we are and what we offer. Our menu is listed on the website. My current menu is 8.5x14 inserts that feature a cover page, 4 inside pages and a back page. I would like something a little more condensed than this. Possibly a large tri-fold menu? I am open to all new ideas. I do have some pictures on my menu now, and would like to continue using a few pictures to feature some of my items. I would like something that is in a format that gives me the option to change items and prices on my own in the future. I would also like it to feature, or inform my patrons about our technology that we offer. We offer online ordering and we are a "verified venue" with Brewvoke.( a social site for craft beer lovers).

Industry/Entity Type

Sports Bar

Requirements
Nice to have
• Nice to have some pictures, but does not have to. We do feature 9 different beers on tap. A lot of them are local craft beers from the state of Kansas. Not sure if that is something we can feature, but it is a nice talking point. All of our tables and bar are hand built. With a rich mahogany finish on all of our woodwork, some type of "woodgrain" look into the menu would be nice.

```html
<!DOCTYPE html>
<html lang="en">
<head>
<meta charset="utf-8">
<title>Harrow Tavern &amp; Grille — Menu</title>
<link rel="stylesheet" href="https://fonts.googleapis.com/css2?family=Cinzel:wght@400;700&family=Oswald:wght@300;400&family=Michroma&display=swap">
<style>
  :root {
    --wood-light: #b06a3c;
    --wood-mid: #8a4524;
    --wood-dark: #5a2612;
    --parchment-light: #e2cfa6;
    --parchment-mid: #cdb283;
    --parchment-edge: #a57d4c;
    --ink: #1d1712;
    --ink-soft: #2e241b;
    --white: #f4efe6;
  }
  * { margin: 0; padding: 0; box-sizing: border-box; }
  html, body { width: 850px; height: 1200px; overflow: hidden; }
  body { background: var(--wood-dark); }
  .menu {
    position: relative; width: 850px; height: 1200px; overflow: hidden;
    background: linear-gradient(180deg, var(--wood-light) 0%, var(--wood-mid) 45%, var(--wood-dark) 100%);
    color: var(--ink);
  }
  .parchment { position: absolute; inset: 0; }
  .brand {
    position: absolute; top: 52px; left: 0; width: 850px; text-align: center;
    font-family: "Cinzel", serif; font-weight: 400; color: var(--ink);
  }
  .brand-name { font-size: 60px; line-height: 60px; }
  .brand-sub { font-size: 20px; letter-spacing: 3px; margin-top: 4px; padding-left: 170px; }
  .section-title {
    position: absolute; font-family: "Cinzel", serif; font-weight: 700;
    font-size: 34px; color: var(--ink); letter-spacing: 0.5px;
  }
  .column { position: absolute; }
  .item { margin-bottom: 6px; }
  .item-name {
    font-family: "Oswald", sans-serif; font-weight: 400; font-size: 15.5px;
    line-height: 17px; text-transform: uppercase; color: var(--ink); letter-spacing: -0.2px;
  }
  .item-desc {
    font-family: "Oswald", sans-serif; font-weight: 300; font-size: 9.3px;
    line-height: 12px; text-transform: uppercase; color: var(--ink-soft);
  }
  .item-price {
    font-family: "Michroma", sans-serif; font-size: 6.4px; line-height: 9px;
    color: var(--ink); letter-spacing: 0.3px;
  }
  .feature-photo { position: absolute; border-radius: 50%; }
  .feature-eggrolls {
    left: 606px; top: 210px; width: 156px; height: 156px;
    background: radial-gradient(circle at 50% 55%, #d9c56a 0%, #8a8c3a 45%, #1c1c14 80%);
  }
  .feature-berry {
    left: 648px; top: 656px; width: 104px; height: 104px;
    background: radial-gradient(circle at 50% 50%, #5a2a3a 0%, #b4472e 40%, #3d6a2a 80%);
  }
  .divider { position: absolute; left: 196px; top: 689px; width: 444px; height: 1px; background: var(--ink); }
  .social {
    position: absolute; top: 1046px; left: 0; width: 850px;
    display: flex; justify-content: center; align-items: center; gap: 14px;
    font-family: "Michroma", sans-serif; font-size: 7.5px; color: var(--ink); letter-spacing: 0.6px;
  }
  .social-mark { width: 18px; height: 18px; background: var(--ink); display: inline-block; }
  .social-entry { display: flex; align-items: center; gap: 12px; }
  .footnote {
    position: absolute; top: 1153px; left: 0; width: 850px; text-align: center;
    font-family: "Michroma", sans-serif; font-size: 6.4px; color: var(--white); letter-spacing: 0.4px;
  }
</style>
</head>
<body>
<main class="menu">
  <svg class="parchment" width="850" height="1200" viewBox="0 0 850 1200" aria-hidden="true">
    <defs>
      <radialGradient id="parchmentTone" cx="50%" cy="50%" r="65%">
        <stop offset="0%" stop-color="#e2cfa6"/>
        <stop offset="70%" stop-color="#cdb283"/>
        <stop offset="100%" stop-color="#a57d4c"/>
      </radialGradient>
    </defs>
    <path fill="url(#parchmentTone)" d="M70 186 L140 196 L210 180 L300 192 L380 183 L470 194 L560 182 L640 192 L700 178 L760 188 L805 210 L798 280 L810 360 L800 450 L812 540 L802 620 L814 700 L804 800 L812 880 L800 960 L808 1040 L792 1100 L720 1112 L640 1098 L560 1110 L470 1098 L380 1112 L300 1100 L220 1112 L140 1100 L70 1108 L44 1060 L54 980 L40 900 L52 820 L42 730 L54 640 L40 550 L52 460 L40 370 L52 290 L42 220 Z"/>
  </svg>

  <header class="brand">
    <div class="brand-name">Harrow</div>
    <div class="brand-sub">TAVERN &amp; GRILLE</div>
  </header>

  <h2 class="section-title" style="left:94px; top:246px;">APPETIZERS</h2>

  <div class="feature-photo feature-eggrolls" role="img" aria-label="Photo of spicy southwest chicken egg rolls with ranch dip"></div>

  <section class="column" style="left:98px; top:298px; width:320px;">
    <div class="item"><div class="item-name">Slider Burgers</div><div class="item-desc">Six juicy bite sized burgers topped with American cheese and served with pickle slices.</div><div class="item-price">8.99</div></div>
    <div class="item"><div class="item-name">Loaded Potato Skins</div><div class="item-desc">Six crispy skins loaded with jack, cheddar and mozzarella cheese, then topped with smoked bacon and green onions. Served with sour cream.</div><div class="item-price">8.99</div></div>
    <div class="item"><div class="item-name">Rattlesnake Eggs</div><div class="item-desc">A spicy combo of pepper jack cheese and jalapeños, battered and fried.</div><div class="item-price">7.99</div></div>
    <div class="item"><div class="item-name">Mozzarella Cheese Sticks</div><div class="item-desc">Classic battered mozzarella cheese sticks served with ranch dressing.</div><div class="item-price">7.99</div></div>
    <div class="item"><div class="item-name">Grand Slam French Fries</div><div class="item-desc">French fries loaded with jack, cheddar, mozzarella, bacon, jalapeños and green onions! Served with ranch dressing.</div><div class="item-price">7.99</div></div>
    <div class="item"><div class="item-name">Bang Bang Shrimp</div><div class="item-desc">Lightly breaded and fried shrimp coated with a spicy Thai sauce, topped with parmesan cheese and diced tomatoes. Served over a bed of romaine lettuce.</div><div class="item-price">7.99</div></div>
    <div class="item"><div class="item-name">Ballpark Pretzel Basket</div><div class="item-desc">Buttered and salted pretzels served with nacho cheese sauce.</div><div class="item-price">7.99</div></div>
  </section>

  <section class="column" style="left:427px; top:298px; width:330px;">
    <div class="item"><div class="item-name">Spicy Southwest<br>Chicken Eggrolls</div><div class="item-desc">Stuffed with black beans, corn and chicken.<br>Served with southwest ranch.</div><div class="item-price">9.99</div></div>
    <div class="item"><div class="item-name">Blooming Onion</div><div class="item-desc">This fan favorite is classically carved and deep fried to perfection. Served with Harrow signature dipping sauce.</div><div class="item-price">7.99</div></div>
    <div class="item"><div class="item-name">Chicken Quesadilla</div><div class="item-desc">A 12 inch flour tortilla stuffed with grilled chicken and jack and cheddar cheese. Served with salsa.</div><div class="item-price">8.99</div></div>
    <div class="item"><div class="item-name">Hollis's Boneless Buffalo Wings</div><div class="item-desc">A full pound of spicy, boneless buffalo wings. Served with ranch dressing or Hollis's gold label sauce.</div><div class="item-price">7.99</div></div>
    <div class="item"><div class="item-name">Harrow Loaded Nachos</div><div class="item-desc">Tri-colored tortilla chips smothered with creamy Monterey jack cheese, choice of beef or chicken, and topped with grilled peppers and onions, jalapeños and diced tomatoes. Served with sour cream and salsa.</div><div class="item-price">9.99</div></div>
    <div class="item"><div class="item-name">Garlic Bread Basket</div><div class="item-desc">Tri-colored tortilla chips smothered with creamy Monterey jack cheese, choice of beef or chicken, and topped with grilled peppers and onions, jalapeños and diced tomatoes. Served with sour cream and salsa.</div><div class="item-price">9.99</div></div>
  </section>

  <div class="divider"></div>
  <div class="feature-photo feature-berry" role="img" aria-label="Photo of summer berry salad with blackberries, strawberries and mandarin oranges"></div>

  <h2 class="section-title" style="left:94px; top:716px;">SALADS</h2>

  <section class="column" style="left:98px; top:770px; width:330px;">
    <div class="item"><div class="item-name">Chicken Tender Garden Salad</div><div class="item-desc">A spring lettuce mix topped with shredded jack and cheddar cheese, garden vegetables, bacon, croutons and egg. With your choice of crispy or grilled chicken.</div><div class="item-price">LARGE 8.99 / SMALL 7.99</div></div>
    <div class="item"><div class="item-name">Nacho Crunchito Salad</div><div class="item-desc">Harrow's unique blend of iceberg lettuce, topped with jack and cheddar cheese, tomatoes, black olives, ranch style beans and creamy Italian dressing. Topped with Crunchito chips</div><div class="item-price">LARGE 8.99 / SMALL 7.99</div></div>
    <div class="item"><div class="item-name">Cobb Salad</div><div class="item-desc">Rows of ham, turkey and roast beef, side by side with baby corn, jack and cheddar cheese, egg slices, garden vegetables, bacon and croutons served over iceberg lettuce.</div><div class="item-price">LARGE 8.99 / SMALL 7.99</div></div>
    <div class="item"><div class="item-name">Summer Berry Salad</div><div class="item-desc">A blend of fresh berries, tomatoes, croutons, mandarin oranges and crumbled feta cheese served on fresh spinach leaves. Your choice of chicken or shrimp.</div><div class="item-price">LARGE 8.99 / SMALL 7.99</div></div>
  </section>

  <section class="column" style="left:427px; top:770px; width:330px;">
    <div class="item"><div class="item-name">House Caesar Salad</div><div class="item-desc">A classic mix of crisp romaine lettuce, shredded parmesan cheese, and croutons. Served with our signature Caesar dressing.</div><div class="item-price">LARGE 6.99 / SMALL 5.99<br>LARGE WITH CHICKEN 8.99 / SMALL WITH CHICKEN 6.99</div></div>
    <div class="item"><div class="item-name">Nacho Crunchito Salad</div><div class="item-desc">Harrow's unique blend of iceberg lettuce, topped with jack and cheddar cheese, tomatoes, black olives, ranch style beans and creamy Italian dressing. Topped with Crunchito chips.</div><div class="item-price">LARGE 8.99 / SMALL 7.99</div></div>
    <div class="item"><div class="item-name">Cobb Salad</div><div class="item-desc">Rows of ham, turkey and roast beef, side by side with baby corn, jack and cheddar cheese, egg slices, garden vegetables, bacon and croutons served over iceberg lettuce.</div><div class="item-price">LARGE 8.99 / SMALL 7.99</div></div>
    <div class="item"><div class="item-name">Summer Berry Salad</div><div class="item-desc">A blend of fresh berries, tomatoes, croutons, mandarin oranges and crumbled feta cheese served on fresh spinach leaves. Your choice of chicken or shrimp.</div><div class="item-price">LARGE 8.99 / SMALL 7.99</div></div>
  </section>

  <footer class="social">
    <div class="social-entry"><span class="social-mark"></span><span>HARROWTAVERNANDGRILLE</span></div>
    <div class="social-entry"><span class="social-mark"></span><span>WWW.HARROWTAVERNCO.EXAMPLE</span></div>
    <div class="social-entry"><span class="social-mark"></span><span>BREWVOKE</span></div>
  </footer>

  <p class="footnote">WHEN SPLITTING A LARGE PORTION, YOU WILL BE CHARGED THE PRICE OF A SMALL PORTION IF A SMALL PORTION IS OFFERED</p>
</main>
</body>
</html>
```